Business Card Design

Looking for business card designs for a new business. there will be two cards of the same design (both lots of information below in contact info). We would like the logo diagonally across the card with the information split above and below the logo similar to sketch. happy to look at similar alternatives
Please use same colours as in logo design

Industry/Entity Type

Business

Contact Information for Business Card

Dwight Halloran
mob - 0491 738 204
ph - 02 6148 3920
fax - 02 6148 3975
email - dwight@kestrelbeams.com.au
14 Larkmoor Road, Taminda NSW 2340

Colin Marchetti
mob - 0438 912 557
ph - 02 6148 3920
fax - 02 6148 3975
email - colin@kestrelbeams.com.au

```html
<!DOCTYPE html>
<html lang="en">
<head>
<meta charset="utf-8">
<title>Kestrel Beams – Business Cards</title>
<link href="https://fonts.googleapis.com/css2?family=Open+Sans:wght@400;600;700;800&display=swap" rel="stylesheet">
<style>
  :root {
    --teal: #0b7b76;
    --ink: #161616;
    --paper: #ffffff;
    --panel: #f2f2f2;
    --backdrop: #e9e7e3;
  }
  * { margin: 0; padding: 0; box-sizing: border-box; }
  html, body {
    width: 1200px; height: 1150px; overflow: hidden;
    background: var(--backdrop);
    font-family: "Open Sans", sans-serif;
  }
  .canvas { position: relative; width: 1200px; height: 1150px; }

  .card { position: absolute; width: 919px; height: 524px; overflow: hidden; }

  /* Front */
  .card--front {
    left: 36px; top: 31px;
    background: var(--paper);
    border: 1px solid #444;
  }
  .stripe { position: absolute; top: 0; bottom: 0; background: var(--teal); }
  .stripe--thin { left: 61px; width: 14px; }
  .stripe--wide { left: 91px; width: 175px; }
  .panel {
    position: absolute; left: 36px; top: 47px;
    width: 288px; height: 326px;
    background: var(--panel);
  }
  .brand {
    position: absolute; display: flex; align-items: center; gap: 16px;
    color: var(--ink); font-weight: 800; letter-spacing: -1px;
  }
  .brand__mark { background: var(--teal); flex: none; }
  .card--front .brand { left: 58px; top: 100px; font-size: 70px; line-height: 1; }
  .card--front .brand__mark { width: 48px; height: 48px; }

  .person {
    position: absolute; left: 57px; top: 300px;
    color: var(--teal); font-size: 28px; font-weight: 700;
  }
  .contact { position: absolute; left: 426px; top: 302px; }
  .contact__row { display: flex; height: 39px; align-items: baseline; }
  .contact__label { width: 82px; color: var(--teal); font-size: 20px; }
  .contact__value { color: var(--ink); font-size: 20px; }
  .address {
    position: absolute; left: 423px; top: 467px;
    color: var(--ink); font-size: 20px;
  }

  /* Back */
  .card--back {
    left: 268px; top: 602px;
    background: var(--teal);
  }
  .card--back .brand {
    left: 0; right: 0; top: 205px; justify-content: center;
    font-size: 86px; line-height: 1;
  }
  .card--back .brand__mark { width: 56px; height: 56px; background: var(--paper); }
  .website {
    position: absolute; left: 0; right: 0; top: 410px;
    text-align: center; color: var(--paper);
    font-size: 30px; letter-spacing: 2px;
  }
  .website strong { font-weight: 600; }
</style>
</head>
<body>
<main class="canvas">

  <section class="card card--front" aria-label="Business card front">
    <div class="stripe stripe--thin"></div>
    <div class="stripe stripe--wide"></div>
    <div class="panel"></div>

    <div class="brand">
      <span class="brand__mark"></span>
      <span class="brand__name">Kestrel Beams</span>
    </div>

    <p class="person">Colin Marchetti</p>

    <div class="contact">
      <div class="contact__row"><span class="contact__label">Phone:</span><span class="contact__value">02 6148 3920</span></div>
      <div class="contact__row"><span class="contact__label">Mobile:</span><span class="contact__value">0438 912 557</span></div>
      <div class="contact__row"><span class="contact__label">Fax:</span><span class="contact__value">02 6148 3975</span></div>
      <div class="contact__row"><span class="contact__label">Email:</span><span class="contact__value">colin@kestrelbeams.com.au</span></div>
    </div>

    <p class="address">14 Larkmoor Road, Taminda NSW 2340</p>
  </section>

  <section class="card card--back" aria-label="Business card back">
    <div class="brand">
      <span class="brand__mark"></span>
      <span class="brand__name">Kestrel Beams</span>
    </div>
    <p class="website">www.<strong>kestrelbeams</strong>.com.au</p>
  </section>

</main>
</body>
</html>
```